Automotive component supplier needs a business card design

We need a business card design for our company called Velran Global Components Ltd based in the UK. We are a supplier of interior and exterior components to premium car manufacturers such as Corvel Ashby, Hadley Fenn, Marquist and Tavarelli. We would like to see a modern business card design that uses the colour blue.

Target Market(s)

Premium automotive car manufacturers.

Industry/Entity Type

Automotive

Contact Information for Business Card

Company Name : Velran Global Components Limited
Address: 17 Marlow Yard, Upper Heath, Warwick, CV31 8QL, United Kingdom
Web Address : www.velrancomponents-example.co.uk

Font styles to use
Other font styles liked:
• Helvetica

Colors
3176b5
0255a3
85acd3
cfdeed
cee9f5
85cae6
34a6d7
0692cd
9bcb3c

Requirements
Must have
• Clear company logo and a mixture of blue colours.
Nice to have
• A high quality modern image.
Should not have
• Multiple colours.

```html
<!DOCTYPE html>
<html lang="en">
<head>
<meta charset="utf-8">
<title>Velran Global Components – Business Card</title>
<link href="https://fonts.googleapis.com/css2?family=Lato:wght@400;700&display=swap" rel="stylesheet">
<style>
  :root {
    --bg: #3b3c3e;
    --brand-blue: #0a86c8;
    --accent-green: #9bcb3c;
    --ink: #1d1d1f;
    --white: #ffffff;
  }
  html, body {
    margin: 0;
    padding: 0;
    width: 1200px;
    height: 800px;
    overflow: hidden;
    background: var(--bg);
    font-family: "Lato", Helvetica, Arial, sans-serif;
  }
  .canvas {
    position: relative;
    width: 1200px;
    height: 800px;
  }
  .card {
    position: absolute;
    width: 560px;
    height: 320px;
    overflow: hidden;
    box-shadow: 0 10px 28px rgba(0,0,0,0.45);
  }
  .brand {
    display: flex;
    align-items: center;
    gap: 12px;
    font-weight: 700;
    line-height: 1;
    white-space: nowrap;
  }
  .brand__mark {
    width: 16px;
    height: 16px;
    background: var(--accent-green);
    flex: none;
  }
  /* Front */
  .card--front {
    left: 70px;
    top: 80px;
    background: var(--brand-blue);
    color: var(--white);
  }
  .card--front .brand {
    position: absolute;
    left: 0;
    right: 0;
    top: 112px;
    justify-content: center;
    font-size: 32px;
    color: var(--white);
    letter-spacing: 0.5px;
  }
  .front__web {
    position: absolute;
    left: 0;
    right: 0;
    bottom: 34px;
    margin: 0;
    text-align: center;
    font-size: 15px;
    letter-spacing: 1.5px;
  }
  /* Back */
  .card--back {
    left: 570px;
    top: 400px;
    background: var(--white);
    color: var(--ink);
  }
  .card__shapes {
    position: absolute;
    inset: 0;
  }
  .card--back .brand {
    position: absolute;
    right: 28px;
    top: 36px;
    font-size: 25px;
    color: var(--brand-blue);
  }
  .holder {
    position: absolute;
    right: 40px;
    top: 118px;
  }
  .holder__name {
    margin: 0;
    font-size: 21px;
    font-weight: 700;
    color: var(--brand-blue);
  }
  .holder__role {
    margin: 2px 0 0;
    font-size: 15px;
  }
  .address {
    position: absolute;
    left: 56px;
    top: 118px;
    margin: 0;
    font-style: normal;
    font-size: 14.5px;
    line-height: 1.3;
  }
  .contacts {
    position: absolute;
    left: 56px;
    top: 194px;
    margin: 0;
    padding: 0;
    list-style: none;
    font-size: 14.5px;
    line-height: 1.3;
  }
  .contacts li {
    display: flex;
    align-items: center;
    gap: 10px;
  }
  .contacts svg {
    width: 12px;
    height: 12px;
    flex: none;
    fill: var(--brand-blue);
  }
</style>
</head>
<body>
<main class="canvas">

  <section class="card card--front" aria-label="Business card front">
    <div class="brand">
      <span class="brand__mark"></span>
      <span class="brand__name">Velran Global Components</span>
    </div>
    <p class="front__web">www.velrancomponents-example.co.uk</p>
  </section>

  <section class="card card--back" aria-label="Business card back">
    <svg class="card__shapes" viewBox="0 0 560 320" aria-hidden="true">
      <path class="swoosh-top" d="M0 0 H160 Q40 50 0 220 Z" fill="var(--brand-blue)"/>
      <path class="swoosh-top-accent" d="M168 2 Q48 55 4 228 Q64 62 168 2 Z" fill="var(--accent-green)"/>
      <path class="swoosh-bottom" d="M0 320 V296 Q260 252 420 240 Q530 228 560 168 V320 Z" fill="var(--brand-blue)"/>
      <path class="swoosh-bottom-accent" d="M360 250 Q500 240 552 168 Q520 232 360 250 Z" fill="var(--accent-green)"/>
      <path d="M0 296 Q260 252 420 240 Q530 228 560 168" fill="none" stroke="var(--white)" stroke-width="4"/>
    </svg>

    <div class="brand">
      <span class="brand__mark"></span>
      <span class="brand__name">Velran Global Components</span>
    </div>

    <div class="holder">
      <p class="holder__name">Martin Keswell</p>
      <p class="holder__role">Manager</p>
    </div>

    <address class="address">
      17 Marlow Yard, Upper Heath<br>
      Warwick, CV31 8QL<br>
      United Kingdom
    </address>

    <ul class="contacts">
      <li>
        <svg viewBox="0 0 24 24"><path d="M6.6 10.8a15.1 15.1 0 0 0 6.6 6.6l2.2-2.2a1 1 0 0 1 1-.25 11.4 11.4 0 0 0 3.6.57 1 1 0 0 1 1 1V20a1 1 0 0 1-1 1A17 17 0 0 1 3 4a1 1 0 0 1 1-1h3.5a1 1 0 0 1 1 1c0 1.25.2 2.45.57 3.57a1 1 0 0 1-.25 1z"/></svg>
        512 004 2710
      </li>
      <li>
        <svg viewBox="0 0 24 24"><path d="M7 1h10a2 2 0 0 1 2 2v18a2 2 0 0 1-2 2H7a2 2 0 0 1-2-2V3a2 2 0 0 1 2-2zm0 3v14h10V4z"/></svg>
        512 004 2711
      </li>
      <li>
        <svg viewBox="0 0 24 24"><path d="M2 5h20v14H2zm2 2v.5l8 5 8-5V7z"/></svg>
        info@velrancomponents-example.co.uk
      </li>
      <li>
        <svg viewBox="0 0 24 24"><path d="M12 2a10 10 0 1 0 0 20 10 10 0 0 0 0-20zm6.9 9h-3a15 15 0 0 0-1.3-5.6A8 8 0 0 1 18.9 11zM12 4c.9 1.2 1.8 3.6 2 7h-4c.2-3.4 1.1-5.8 2-7zM4.1 13h3a15 15 0 0 0 1.3 5.6A8 8 0 0 1 4.1 13zm3-2h-3a8 8 0 0 1 4.3-5.6A15 15 0 0 0 7.1 11zM12 20c-.9-1.2-1.8-3.6-2-7h4c-.2 3.4-1.1 5.8-2 7zm2.6-1.4a15 15 0 0 0 1.3-5.6h3a8 8 0 0 1-4.3 5.6z"/></svg>
        www.velrancomponents-example.co.uk
      </li>
    </ul>
  </section>

</main>
</body>
</html>
```